Want a package created for a new protein bar

We would like a new package created for a new protein bar project The name of the bar will be VORNBar a real food protein bar, we would like a ‘window’ on the package of bar like Bold Meadow bar below in images.

VORNBar
‘Super Food Bar’
14g of Whey Protein
The package film size is the following 12cm width x 15cm Length,
Flavor Peanut Chocolate Chip, additional information will be attached shortly like nutrition facts,

Target Market(s)

fitness market, bodybuilders, athletes, everyday people

Industry/Entity Type

Health Product

Logo Text

VORNBar

Font styles to use
Serif
Sans Serif
Decorative

Requirements
Must have
• Package window

```html
<!DOCTYPE html>
<html lang="en">
<head>
<meta charset="utf-8">
<title>VORNBar Super Food Bar Wrapper</title>
<link rel="stylesheet" href="https://fonts.googleapis.com/css2?family=Russo+One&display=swap">
<style>
  :root {
    --backdrop: #f2f2f2;
    --wrapper-black: #121212;
    --wrapper-edge: #1c1c1c;
    --gold: #d4a82a;
    --gold-light: #e9c75a;
    --gold-strip: #e2c04c;
    --window-dark: #4a2414;
    --window-mid: #8a4a2a;
    --window-light: #b8895a;
    --icon-line: #1a1a1a;
  }
  html, body {
    margin: 0;
    padding: 0;
    width: 1200px;
    height: 900px;
    overflow: hidden;
    background: var(--backdrop);
  }
  .canvas {
    position: relative;
    width: 1200px;
    height: 900px;
  }
  .wrapper {
    position: absolute;
    left: 267px;
    top: 362px;
    width: 708px;
    height: 185px;
  }
  .wrapper-shape {
    position: absolute;
    inset: 0;
  }
  .brand-block {
    position: absolute;
    left: 70px;
    top: 10px;
    width: 400px;
    font-family: "Russo One", sans-serif;
    color: var(--gold);
  }
  .brand-name {
    position: absolute;
    left: 32px;
    top: 0;
    margin: 0;
    font-size: 60px;
    line-height: 1;
    font-weight: 400;
    letter-spacing: 0;
  }
  .tagline {
    position: absolute;
    left: 10px;
    top: 66px;
    margin: 0;
    font-size: 38px;
    line-height: 1;
    font-weight: 400;
    color: var(--gold-light);
  }
  .details {
    position: absolute;
    left: 68px;
    top: 116px;
    margin: 0;
    font-size: 19px;
    line-height: 25px;
    color: var(--gold-light);
  }
  .product-window {
    position: absolute;
    left: 468px;
    top: 0;
    width: 132px;
    height: 185px;
    background: linear-gradient(160deg, var(--window-light) 0%, var(--window-mid) 40%, var(--window-dark) 75%, var(--window-mid) 100%);
    border-left: 3px solid var(--gold);
    box-sizing: border-box;
  }
  .icon-strip {
    position: absolute;
    left: 600px;
    top: 0;
    width: 57px;
    height: 185px;
    background: linear-gradient(90deg, var(--gold) 0%, var(--gold-strip) 50%, var(--gold) 100%);
  }
  .icon-strip svg {
    position: absolute;
    left: 0;
    width: 57px;
  }
</style>
</head>
<body>
<div class="canvas">
  <div class="wrapper">
    <svg class="wrapper-shape" viewBox="0 0 708 185" width="708" height="185" aria-hidden="true">
      <polygon fill="var(--wrapper-black)" points="
        0,0 40,0 668,0 708,0
        700,9 708,18 700,27 708,36 700,45 708,54 700,63 708,72 700,81 708,90 700,99 708,108 700,117 708,126 700,135 708,144 700,153 708,162 700,171 708,185
        0,185
        8,171 0,162 8,153 0,144 8,135 0,126 8,117 0,108 8,99 0,90 8,81 0,72 8,63 0,54 8,45 0,36 8,27 0,18 8,9"/>
      <line x1="54" y1="0" x2="54" y2="185" stroke="var(--wrapper-edge)" stroke-width="2"/>
      <line x1="660" y1="0" x2="660" y2="185" stroke="var(--wrapper-edge)" stroke-width="2"/>
    </svg>

    <div class="brand-block">
      <h1 class="brand-name">VORNBar</h1>
      <p class="tagline">Super Food Bar</p>
      <p class="details">Peanut Chocolate Chip<br>14g of Whey Protein</p>
    </div>

    <div class="product-window" role="img" aria-label="Clear window showing the peanut chocolate chip bar with nuts, seeds and crisp pieces"></div>

    <div class="icon-strip">
      <svg style="top:14px" viewBox="0 0 57 72" height="72" aria-hidden="true" fill="none" stroke="var(--icon-line)" stroke-width="2" stroke-linejoin="round">
        <rect x="22" y="2" width="14" height="8" rx="1.5"/>
        <path d="M20 10 h18 v6 l5 6 v44 a3 3 0 0 1 -3 3 h-22 a3 3 0 0 1 -3 -3 v-44 l5 -6 z"/>
        <line x1="15" y1="30" x2="43" y2="30"/>
        <line x1="15" y1="58" x2="43" y2="58"/>
        <path d="M31 36 l-5 9 h6 l-5 9"/>
      </svg>
      <svg style="top:104px" viewBox="0 0 57 72" height="72" aria-hidden="true" fill="none" stroke="var(--icon-line)" stroke-width="2" stroke-linejoin="round">
        <rect x="25" y="2" width="7" height="6"/>
        <rect x="13" y="8" width="31" height="14" rx="4"/>
        <line x1="28.5" y1="22" x2="28.5" y2="50"/>
        <rect x="13" y="50" width="31" height="14" rx="4"/>
        <rect x="25" y="64" width="7" height="6"/>
      </svg>
    </div>
  </div>
</div>
</body>
</html>
```